Managed IT services business card design

We haven't needed a business card since the founding of the business in 2005. All our clients have been coming through word of mouth. And lately more and more existing clients are requesting for our business cards to pass on to their contacts in recommending us.
So we needing a business card design. We use various innovative solutions and methodologies to provide IT services to small businesses in managing their IT systems. Our role is the same as an in-house, full-time IT Manager for our clients, but outsourced. So we take care of all our clients' IT needs, just as an IT Manager would be expected to perform.
We have a holding website, which we're happy to leave for now. If we can use the same logo would be great - www.lumadesk.com.au
Preferred colours are shades of are white, grey and black.
We pride our business with the following traits: proactive, good service, prompt response, trustworthy.
Target Market(s)
Small businesses of any industry
Industry/Entity Type
Business

```html
<!DOCTYPE html>
<html lang="en">
<head>
<meta charset="utf-8">
<title>Lumadesk business card</title>
<link rel="stylesheet" href="https://fonts.googleapis.com/css2?family=Questrial&display=swap">
<style>
  :root {
    --page-bg: #d9d9d9;
    --card-bg: #231f1e;
    --ink: #ffffff;
    --ink-soft: #e6e6e6;
    --shadow: rgba(0, 0, 0, 0.28);
  }
  * { box-sizing: border-box; margin: 0; padding: 0; }
  html, body {
    width: 1200px;
    height: 680px;
    overflow: hidden;
  }
  body {
    background: var(--page-bg);
    font-family: "Questrial", "Helvetica Neue", Arial, sans-serif;
    color: var(--ink);
    display: flex;
    align-items: center;
    justify-content: center;
    gap: 56px;
  }
  .card {
    position: relative;
    width: 520px;
    height: 300px;
    background: var(--card-bg);
    border-radius: 18px;
    box-shadow: 0 10px 24px var(--shadow);
    overflow: hidden;
  }
  .wordmark {
    position: absolute;
    font-size: 46px;
    letter-spacing: 0.22em;
    line-height: 1;
    color: var(--ink);
  }

  /* Front: contact side */
  .card--front .wordmark {
    left: 40px;
    top: 186px;
    font-size: 40px;
  }
  .accent-bar {
    position: absolute;
    right: 18px;
    top: 0;
    width: 14px;
    height: 178px;
    background: var(--ink);
  }
  .contact {
    position: absolute;
    right: 48px;
    top: 30px;
    text-align: right;
  }
  .contact__name {
    font-size: 19px;
    letter-spacing: 0.04em;
  }
  .contact__role {
    font-size: 12px;
    color: var(--ink-soft);
    margin-bottom: 16px;
  }
  .contact__address {
    font-size: 13px;
    line-height: 1.3;
    margin-bottom: 14px;
  }
  .contact__list {
    list-style: none;
    font-size: 13px;
    line-height: 1.32;
  }
  .contact__list li {
    display: flex;
    justify-content: flex-end;
    align-items: center;
    gap: 6px;
  }
  .contact__list svg {
    width: 11px;
    height: 11px;
    fill: var(--ink);
    flex: none;
  }
  .contact__list .spacer { width: 11px; flex: none; }

  /* Back: brand side */
  .card--back .wordmark {
    left: 50%;
    top: 118px;
    transform: translateX(-50%);
  }
  .card--back .web {
    position: absolute;
    right: 40px;
    bottom: 32px;
    font-size: 12px;
    letter-spacing: 0.3em;
  }
</style>
</head>
<body>

  <section class="card card--front" aria-label="Business card front">
    <div class="accent-bar"></div>
    <div class="contact">
      <p class="contact__name">Mark Ellison</p>
      <p class="contact__role">director</p>
      <p class="contact__address">14 Harbour Lane<br>Carlton VIC 3053</p>
      <ul class="contact__list">
        <li>03 9000 4120
          <svg viewBox="0 0 12 12" aria-label="phone"><path d="M3 1 L5 3.5 L4 5 Q5 7 7 8 L8.5 7 L11 9 L9.5 11 Q4 10.5 1 2.5 Z"/></svg>
        </li>
        <li>03 9000 4121
          <svg viewBox="0 0 12 12" aria-label="fax"><rect x="3" y="1" width="6" height="4"/><rect x="1" y="5" width="10" height="5" rx="1"/></svg>
        </li>
        <li>info@lumadesk.com.au
          <svg viewBox="0 0 12 12" aria-label="email"><path d="M1 3 H11 V10 H1 Z M1.5 3.5 L6 7 L10.5 3.5" stroke="#231f1e" stroke-width="0.8"/></svg>
        </li>
        <li>www.lumadesk.com.au
          <svg viewBox="0 0 12 12" aria-label="web"><circle cx="6" cy="6" r="5"/><path d="M1 6 H11 M6 1 V11" stroke="#231f1e" stroke-width="0.8"/></svg>
        </li>
      </ul>
    </div>
    <p class="wordmark">lumadesk</p>
  </section>

  <section class="card card--back" aria-label="Business card back">
    <p class="wordmark">lumadesk</p>
    <p class="web">www.lumadesk.com.au</p>
  </section>

</body>
</html>
```